Business Card Design

Hi I need a business card designed, we already have the business name logo artwork and would like some concept ideas for the Bus Card layout.
On the back of the card i want to include the products and services that we offer.
We are a Plastics Sheeting manufacture based in Perth Australia.

                                       

We need a BC design for a company called Tarvo Plastics based in Perth Australia.

We supply from DIY to Trade & Industrial  Engineering Markets.

We specialise in:

·         Cut to size panels  (all shapes and sizes)

·         Plastics fabrication & Welding

·         Custom Designs

·         Plastic Repairs

·         PVC Pipe Slotting & PVC Pipe Threading

·         Supplier of all types of engineering plastics and profiles.

Including:           Acrylic / Clarvene

                               Polycarbonate / Dorvil

                               Prismatic Light Diffuser

                               Vantrib

                               HDPE / UHMWPE

                               PVC / PVC Foam

                               Nylon

                               HIPS

```html
<!DOCTYPE html>
<html lang="en">
<head>
<meta charset="utf-8">
<title>Tarvo Plastics – Business Card</title>
<link rel="stylesheet" href="https://fonts.googleapis.com/css2?family=Source+Sans+3:wght@400;600;700&display=swap">
<style>
  :root {
    --navy: #1c2f6b;
    --orange: #e2761b;
    --ink: #555a60;
    --rule: #c9ccd2;
    --card: #ffffff;
    --stage: #eceae6;
    --ghost: #f0f1f3;
  }
  * { box-sizing: border-box; margin: 0; padding: 0; }
  html, body { width: 1200px; height: 720px; overflow: hidden; }
  body {
    background: var(--stage);
    font-family: "Source Sans 3", "Myriad Pro", Arial, sans-serif;
    display: flex;
    align-items: center;
    justify-content: center;
    gap: 40px;
  }
  .card {
    position: relative;
    width: 540px;
    height: 310px;
    background: var(--card);
    box-shadow: 0 2px 10px rgba(0,0,0,.12);
    overflow: hidden;
  }

  /* Front */
  .ghost-mark {
    position: absolute;
    left: 150px; top: 40px;
    width: 220px; height: 220px;
    background: var(--ghost);
  }
  .double-rule {
    position: absolute;
    width: 6px;
    border-left: 2px solid var(--navy);
    border-right: 2px solid var(--navy);
  }
  .rule-name { left: 36px; top: 58px; height: 70px; }
  .rule-address { right: 36px; top: 30px; height: 80px; }
  .rule-contact { left: 36px; top: 180px; height: 92px; }

  .identity { position: absolute; left: 56px; top: 66px; }
  .identity .name { color: var(--navy); font-weight: 700; font-size: 21px; line-height: 1.1; }
  .identity .title { color: var(--orange); font-weight: 600; font-size: 14px; }

  .address {
    position: absolute; right: 56px; top: 32px;
    text-align: right; color: var(--ink); font-size: 14px; line-height: 1.32;
  }
  .address .po { margin-top: 6px; }

  .contact {
    position: absolute; left: 56px; top: 180px;
    color: var(--ink); font-size: 14px; line-height: 1.36;
  }

  /* Back */
  .brand {
    position: absolute; top: 22px; left: 0; right: 0;
    display: flex; align-items: center; justify-content: center; gap: 12px;
  }
  .brand .square { width: 30px; height: 30px; background: var(--navy); }
  .brand .name { color: var(--navy); font-weight: 700; font-size: 40px; letter-spacing: .5px; line-height: 1; }

  .tagline {
    position: absolute; top: 82px; left: 0; right: 0;
    text-align: center; color: var(--navy); font-weight: 700;
    font-size: 15px; line-height: 1.25;
  }
  .column { position: absolute; top: 130px; }
  .column h2 { color: var(--navy); font-weight: 700; font-size: 18px; margin-bottom: 4px; }
  .services { left: 26px; width: 300px; }
  .materials { left: 360px; top: 122px; }
  .divider {
    position: absolute; left: 340px; top: 118px; height: 150px;
    border-left: 1px solid var(--rule);
  }
  .bullets { list-style: none; color: var(--ink); font-size: 13.5px; line-height: 1.3; }
  .bullets li { position: relative; padding-left: 14px; }
  .bullets li::before {
    content: ""; position: absolute; left: 0; top: 6px;
    width: 6px; height: 6px; border-radius: 50%; background: var(--orange);
  }
  .bullets .pair { display: flex; gap: 12px; padding-left: 0; }
  .bullets .pair::before { display: none; }
  .bullets .pair span { position: relative; padding-left: 14px; }
  .bullets .pair span::before {
    content: ""; position: absolute; left: 0; top: 6px;
    width: 6px; height: 6px; border-radius: 50%; background: var(--orange);
  }
</style>
</head>
<body>

<section class="card card-front">
  <div class="ghost-mark" aria-hidden="true"></div>

  <span class="double-rule rule-name"></span>
  <div class="identity">
    <p class="name">Your Name</p>
    <p class="title">Title</p>
  </div>

  <span class="double-rule rule-address"></span>
  <address class="address">
    <p>Unit 4/18 Marrow Circuit</p>
    <p>Bellgrove WA 6150</p>
    <p class="po">PO Box 2240 Bellgrove</p>
    <p>DC WA 6960</p>
  </address>

  <span class="double-rule rule-contact"></span>
  <div class="contact">
    <p>08 9400 3110</p>
    <p>0412 345 678</p>
    <p>08 9400 3122</p>
    <p>sales@tarvoplastics.com.au</p>
    <p>Kelmar Pty Ltd T/A Tarvo Plastics ABN: TBA</p>
  </div>
</section>

<section class="card card-back">
  <div class="brand">
    <span class="square" aria-hidden="true"></span>
    <span class="name">Tarvo Plastics</span>
  </div>

  <p class="tagline">The Products And Services That We Offer<br>Are Supplied From Diy To Trade &amp; Industrial Engineering Markets</p>

  <div class="column services">
    <h2>We specialise in:</h2>
    <ul class="bullets">
      <li>Cut to size panels (all shapes and sizes)</li>
      <li>Plastics fabrication &amp; Welding</li>
      <li>Custom Designs</li>
      <li>Plastic Repairs</li>
      <li>PVC Pipe Slotting &amp; PVC Pipe Threading</li>
      <li>Supplier of all types of engineering plastics and profiles</li>
    </ul>
  </div>

  <span class="divider" aria-hidden="true"></span>

  <div class="column materials">
    <h2>Including:</h2>
    <ul class="bullets">
      <li>Acrylic / Clarvene</li>
      <li>Polycarbonate / Dorvil</li>
      <li>Prismatic Light Diffuser</li>
      <li class="pair"><span>Vantrib</span><span>HDPE / UHMWPE</span></li>
      <li>PVC / PVC Foam</li>
      <li class="pair"><span>Nylon</span><span>HIPS</span></li>
    </ul>
  </div>
</section>

</body>
</html>
```